Calder Vossik - Cinematographer

NEED:
I'm looking for a sleek, professional, modern business card that will give give the recipient the impression that they can trust their production will go smoothly by hiring me. I will bring creativity and knowledge to their shoot, so that we can create powerful images.
I am looking for a card with a strong style and design ethos that could be expanded to a website and a full visual/graphic/design entity for me.
ABOUT ME:
I am a mid-twenties cinematographer, I work on music video, narrative short, commercial, and corporate projects. I blend the science and artistry of cameras and filmmaking to tell a story. I'm an artist, a technician, and a manager.
DESIGN:
I like sleek, simple design. Black, dark grays, white, dark navy, steel blues, I love cyan, but also cyan and red. I am not a fan of earthy tones. I generally prefer modern, san-serif fonts over serifs. My old logo was based on an aperture, a multi-blade device at the back of a lens that controls how much light passes through, but I made it with so many colors, that it doesn't necessarily lend itself to a specific color-scheme or design ethos. I liked that the aperture design provided a sense of the technical requirements of my job. I'm a fan of matte business cards, but am open to plenty of specialty print processes to make an outstanding card.
ATTACHED FILES:
My Old Rainbox Aperture Logo, plus a few designs I've tried playing around with, but am not tied to. I AM OPEN TO NEW DESIGNS, DO NOT FEEL TIED TO THIS.
**I've pulled my old logo down from the attached files, and instead attached other business cards I like, so as not to mislead you where I would like to go.
INFO:
Name: Calder Vossik
Job: Cinematographer
Email: ccvossik@lumenpost.net
Phone: 415.555.0193
Website: caldervossik.com
Updates
I'm adding some images of other cards that I like, and removing my old logo, since I'm looking for something new, and don't want that old logo to push anyone a certain direction.

```html
<!DOCTYPE html>
<html lang="en">
<head>
<meta charset="utf-8">
<title>Calder Vossik – Cinematographer business card</title>
<link rel="stylesheet" href="https://fonts.googleapis.com/css2?family=Montserrat:wght@400;500;700&family=Open+Sans:wght@400;600;700&display=swap">
<style>
  :root {
    --backdrop: #d9d9dc;
    --card-black: #121214;
    --card-graphite: #2a2a2e;
    --ink-white: #ffffff;
    --ink-soft: #cfd2d6;
    --accent-cyan: #1a9be0;
    --accent-red: #e2413d;
  }
  * { box-sizing: border-box; margin: 0; padding: 0; }
  html, body { width: 1200px; height: 913px; overflow: hidden; }
  body {
    background: var(--backdrop);
    font-family: "Open Sans", Arial, sans-serif;
    position: relative;
  }
  .card {
    position: absolute;
    top: 307px;
    width: 520px;
    height: 298px;
    border-radius: 4px;
    overflow: hidden;
    background: linear-gradient(135deg, var(--card-graphite) 0%, var(--card-black) 55%, #050506 100%);
    box-shadow: 0 10px 28px rgba(0,0,0,.28);
  }
  .card--front { left: 60px; }
  .card--back { left: 620px; }

  /* Front */
  .wordmark {
    position: absolute;
    left: 50%;
    top: 50%;
    transform: translate(-50%, -50%);
    display: flex;
    align-items: center;
    gap: 18px;
  }
  .wordmark__dot {
    width: 64px; height: 64px;
    border-radius: 50%;
    background: var(--accent-cyan);
    flex: none;
  }
  .wordmark__text { display: flex; flex-direction: column; }
  .wordmark__name {
    font-family: "Montserrat", Arial, sans-serif;
    font-weight: 700;
    font-size: 34px;
    letter-spacing: 1px;
    color: var(--ink-white);
    text-transform: uppercase;
    line-height: 1.05;
  }
  .wordmark__role {
    font-family: "Montserrat", Arial, sans-serif;
    font-weight: 400;
    font-size: 17px;
    letter-spacing: 5px;
    color: var(--ink-soft);
    text-transform: uppercase;
    margin-top: 4px;
  }

  /* Back */
  .card__bands { position: absolute; inset: 0; }
  .brand-mini {
    position: absolute;
    right: 34px;
    top: 44px;
    display: flex;
    align-items: center;
    gap: 9px;
  }
  .brand-mini__dot {
    width: 34px; height: 34px;
    border-radius: 50%;
    background: var(--accent-cyan);
  }
  .brand-mini__name {
    font-family: "Montserrat", Arial, sans-serif;
    font-weight: 700;
    font-size: 15px;
    letter-spacing: .5px;
    color: var(--ink-white);
    text-transform: uppercase;
  }
  .identity { position: absolute; left: 34px; top: 120px; color: var(--ink-white); }
  .identity__name { font-weight: 700; font-size: 20px; }
  .identity__role { font-weight: 600; font-size: 12px; margin-top: 6px; }
  .contacts { position: absolute; left: 34px; top: 198px; list-style: none; }
  .contacts__item {
    display: flex; align-items: center; gap: 12px;
    color: var(--ink-white);
    font-size: 13px;
    line-height: 22px;
  }
  .contacts__icon { width: 13px; height: 13px; flex: none; }
</style>
</head>
<body>
  <section class="card card--front" aria-label="Card front">
    <div class="wordmark">
      <span class="wordmark__dot"></span>
      <div class="wordmark__text">
        <span class="wordmark__name">Calder Vossik</span>
        <span class="wordmark__role">Cinematographer</span>
      </div>
    </div>
  </section>

  <section class="card card--back" aria-label="Card back">
    <svg class="card__bands" viewBox="0 0 520 298" width="520" height="298" aria-hidden="true">
      <path d="M250,0 L520,0 L520,52 Q400,14 250,0 Z" fill="var(--accent-cyan)"/>
      <path d="M250,0 Q400,14 520,52 L520,62 Q395,22 250,0 Z" fill="var(--accent-red)"/>
      <path d="M330,298 Q450,258 520,190 L520,298 Z" fill="var(--accent-cyan)"/>
      <path d="M310,298 Q440,252 520,174 L520,190 Q450,258 330,298 Z" fill="var(--accent-red)"/>
    </svg>

    <div class="brand-mini">
      <span class="brand-mini__dot"></span>
      <span class="brand-mini__name">Calder Vossik</span>
    </div>

    <div class="identity">
      <p class="identity__name">Calder Vossik</p>
      <p class="identity__role">Cinematographer</p>
    </div>

    <ul class="contacts">
      <li class="contacts__item">
        <svg class="contacts__icon" viewBox="0 0 16 16" aria-hidden="true"><path d="M3 1 L6 1 L7 5 L5 6.5 Q6.5 9.5 9.5 11 L11 9 L15 10 L15 13 Q15 15 13 15 Q2 14 1 3 Q1 1 3 1 Z" fill="var(--accent-cyan)"/></svg>
        <span>415.555.0193</span>
      </li>
      <li class="contacts__item">
        <svg class="contacts__icon" viewBox="0 0 16 16" aria-hidden="true"><rect x="1" y="3" width="14" height="10" rx="1" fill="var(--accent-cyan)"/><path d="M1.5 3.5 L8 9 L14.5 3.5" fill="none" stroke="var(--card-black)" stroke-width="1.3"/></svg>
        <span>ccvossik@lumenpost.net</span>
      </li>
      <li class="contacts__item">
        <svg class="contacts__icon" viewBox="0 0 16 16" aria-hidden="true"><circle cx="8" cy="8" r="7" fill="var(--accent-cyan)"/><path d="M1 8 H15 M8 1 V15 M8 1 Q3 8 8 15 M8 1 Q13 8 8 15" fill="none" stroke="var(--card-black)" stroke-width="1"/></svg>
        <span>www.caldervossik.com</span>
      </li>
    </ul>
  </section>
</body>
</html>
```